Australian Trucking Company Requires Professional Looking Stationary

We require a professional looking stationary design that incorporates our newly designed logo.

Our business, called "Brell Haulage Contracting", provides contracting work, transport and logistics to business in Western Australia particularly with links to the mining sector.

We are a small business looking to expand and our new logo and our new stationary will help develop our brand image in our market place.

Target Market(s)

Businesses and Corporation with links to the Mining Sector

Industry/Entity Type

Small Business

Requirements
Must have
• The letterhead must have the following details:
The new logo

Text saying: "Brell Holdings Pty Ltd (ACN 582 316 907) ATF The Brell Discretionary Trust T/AS"
"ABN 71 834 209 553"
Address "P.O Box 817 Wattlegrove WA, 6958"
Phone: 08 9352 7140
Email: brellhaul@mailbox-example.com.au

The text on the letterhead should be editable as the details are likely to change in the near future. Provision should be made for a website address all though one isn't available at the moment.

The styling, layout and font text is entirely up to the designer.

```html
<!DOCTYPE html>
<html lang="en">
<head>
<meta charset="utf-8">
<title>Brell Haulage Contracting – Business Cards</title>
<link rel="stylesheet" href="https://fonts.googleapis.com/css2?family=Roboto:wght@400;500;700;900&display=swap">
<style>
  :root {
    --backdrop: #e9e6e2;
    --card: #ffffff;
    --brand-red: #a51d24;
    --band-red: #b41f26;
    --bright-red: #e3202c;
    --stripe-grey: #6d6d6f;
    --text-grey: #a9a9a9;
    --mark-grey: #8a8a8c;
    --white: #ffffff;
  }
  * { box-sizing: border-box; margin: 0; padding: 0; }
  html, body { width: 1200px; height: 665px; overflow: hidden; }
  body {
    background: var(--backdrop);
    font-family: "Roboto", Arial, sans-serif;
    position: relative;
  }
  .card {
    position: absolute;
    width: 560px;
    height: 320px;
    background: var(--card);
    overflow: hidden;
    box-shadow: 0 6px 18px rgba(0,0,0,0.18);
  }
  .card--front { left: 24px; top: 120px; }
  .card--back  { left: 616px; top: 225px; }
  .card__waves { position: absolute; inset: 0; width: 100%; height: 100%; }

  .brand { position: absolute; display: flex; align-items: center; }
  .brand__square { background: var(--mark-grey); flex: none; }
  .brand__name {
    color: var(--brand-red);
    font-weight: 900;
    text-transform: uppercase;
    line-height: 0.98;
  }
  .card--front .brand { left: 34px; top: 34px; gap: 16px; }
  .card--front .brand__square { width: 40px; height: 40px; }
  .card--front .brand__name { font-size: 24px; }

  .card--back .brand { left: 70px; top: 100px; gap: 22px; }
  .card--back .brand__square { width: 58px; height: 58px; }
  .card--back .brand__name { font-size: 40px; }

  .person { position: absolute; right: 60px; top: 22px; text-align: right; }
  .person__name { color: var(--brand-red); font-weight: 700; font-size: 17px; }
  .person__title { color: var(--brand-red); font-size: 11px; margin-top: 1px; }

  .contact { position: absolute; right: 40px; top: 76px; list-style: none; text-align: right; }
  .contact__item {
    display: flex; justify-content: flex-end; align-items: center; gap: 6px;
    color: var(--brand-red); font-size: 12px; line-height: 20px;
  }
  .contact__icon { width: 11px; height: 11px; flex: none; }

  .entity { position: absolute; left: 34px; top: 142px; color: var(--text-grey); font-size: 12px; line-height: 17px; }
  .postal { position: absolute; left: 210px; top: 194px; color: var(--text-grey); font-size: 12px; }
  .abn { position: absolute; left: 34px; top: 291px; color: var(--white); font-size: 12px; }

  .web { position: absolute; left: 62px; top: 276px; color: var(--white); font-size: 13px; letter-spacing: 0.5px; }
  .web strong { font-weight: 700; font-size: 15px; }
</style>
</head>
<body>

<section class="card card--front" aria-label="Business card front">
  <svg class="card__waves" viewBox="0 0 560 320" aria-hidden="true">
    <path d="M330 238 C420 226 500 200 560 172 L560 140 C490 184 410 222 330 238 Z" fill="var(--bright-red)"/>
    <path d="M0 262 C160 236 400 268 560 185 L560 196 C400 280 160 248 0 274 Z" fill="var(--stripe-grey)"/>
    <path d="M0 280 C160 254 400 286 560 204 L560 320 L0 320 Z" fill="var(--band-red)"/>
  </svg>

  <div class="brand">
    <span class="brand__square"></span>
    <span class="brand__name">Brell<br>Haulage<br>Contracting</span>
  </div>

  <div class="person">
    <p class="person__name">Name here</p>
    <p class="person__title">Title</p>
  </div>

  <ul class="contact">
    <li class="contact__item">08 9352 7140
      <svg class="contact__icon" viewBox="0 0 12 12" aria-hidden="true"><circle cx="6" cy="6" r="5.5" fill="none" stroke="var(--bright-red)"/><path d="M3.8 3.2 L5 3 L5.5 4.6 L4.8 5.2 C5.2 6 5.9 6.8 6.8 7.2 L7.4 6.5 L9 7 L8.8 8.3 C6 8.3 3.8 6 3.8 3.2Z" fill="var(--bright-red)"/></svg>
    </li>
    <li class="contact__item">brellhaul@mailbox-example.com.au
      <svg class="contact__icon" viewBox="0 0 12 12" aria-hidden="true"><rect x="1" y="2.5" width="10" height="7" fill="var(--bright-red)"/><path d="M1 2.5 L6 6.5 L11 2.5" fill="none" stroke="var(--white)" stroke-width="0.9"/></svg>
    </li>
    <li class="contact__item">www.brellhaulage.com
      <svg class="contact__icon" viewBox="0 0 12 12" aria-hidden="true"><circle cx="6" cy="6" r="5" fill="var(--bright-red)"/><path d="M1 6 H11 M6 1 C3.5 4 3.5 8 6 11 M6 1 C8.5 4 8.5 8 6 11" fill="none" stroke="var(--white)" stroke-width="0.7"/></svg>
    </li>
  </ul>

  <p class="entity">Brell Holdings Pty Ltd<br>(ACN 582 316 907)<br>ATF The Brell Discretionary Trust T/AS</p>
  <p class="postal">P.O Box 817 Wattlegrove WA, 6958</p>
  <p class="abn">ABN 71 834 209 553</p>
</section>

<section class="card card--back" aria-label="Business card back">
  <svg class="card__waves" viewBox="0 0 560 320" aria-hidden="true">
    <path d="M0 243 C120 205 230 215 340 252 C430 282 500 282 560 276 L560 282 C490 288 420 288 330 258 C220 222 120 212 0 250 Z" fill="var(--stripe-grey)"/>
    <path d="M0 252 C120 217 220 227 330 262 C420 292 490 292 560 287 L560 320 L0 320 Z" fill="var(--band-red)"/>
    <path d="M380 262 C450 274 510 268 560 254 L560 272 C500 283 440 281 380 262 Z" fill="var(--bright-red)"/>
  </svg>

  <div class="brand">
    <span class="brand__square"></span>
    <span class="brand__name">Brell<br>Haulage<br>Contracting</span>
  </div>

  <p class="web">www.<strong>brellhaulage</strong>.com</p>
</section>

</body>
</html>
```